Killer Webpage Design

I currently have a self-hosted webpage through wordpress at www.velmarqstudio.com - the content is complete and I'm happy with this but I need it designed (no coding) to complete my requirements. I'm happy to take designs which are non-Wordpress if there is specific advantage in this.

My full branding logos are attached along with color files. My main aim is consistent branding across all areas (social media, business cards, emails, websites). I have the rest running but am not happy with the available default selections from Wordpress.

I would prefer to use the darker blue version of the logo as I feel this has more standout in online media, however I would appreciate submissions with both variants to help me choose.

With the homepage I will also want to see blog pages and category pages designed but this can come after I have selected a design to go with,

Sites that I like and are related to my business include the following:
http://www.brindlepath.com/au/accounting-software/
http://www.tasklanternpro.com/home.aspx
https://pelicoin.com/register
Updates

Apologies for the confusion - to clarify for designers I am looking for design only, no coding.

FYI - i have now uploaded business cards for an idea of the contemporary style of design completed so far.

Target Market(s)

small to medium business. Not systemised but looking for help and support.

Industry/Entity Type

Business

Requirements
Must have
• I'm looking for a minimalist professional page, with the ability to easily add new sections when required. I will also need a CMS to add blog posts on the go, with the same features that it currently has (comments, social logon etc)

```html
<!DOCTYPE html>
<html lang="en">
<head>
<meta charset="utf-8">
<title>Velmarq Studio</title>
<link href="https://fonts.googleapis.com/css2?family=Poppins:wght@400;500;600&family=Arimo:wght@400&display=swap" rel="stylesheet">
<style>
:root{
  --navy:#0f2c3d;
  --nav-bg:#1c3e50;
  --teal:#14b3c4;
  --grey-text:#7a7a7a;
  --body-text:#6b6b6b;
  --rule:#d9d9d9;
  --footer-bg:#e9e9e9;
  --icon-grey:#8a8a8a;
}
*{margin:0;padding:0;box-sizing:border-box}
html,body{width:1200px;height:1067px;overflow:hidden;background:#fff}
body{position:relative;font-family:"Arimo",Arial,sans-serif;color:var(--body-text)}
.nav{position:absolute;left:0;top:0;width:1200px;height:35px;background:var(--nav-bg)}
.nav ul{list-style:none;display:flex;position:absolute;left:200px;top:0;height:35px;align-items:center}
.nav li{font-size:12px;color:#9fb4bf;padding:0 16px;border-left:1px solid #2f5366;line-height:14px;white-space:nowrap}
.nav li:first-child{padding-left:0;border:0;color:#fff}
.nav li:last-child{padding-right:0}
.header{position:absolute;left:0;top:35px;width:1200px;height:69px;background:linear-gradient(#fff,#ececec);border-bottom:1px solid #d4d4d4;box-shadow:0 1px 3px rgba(0,0,0,.12)}
.brand{position:absolute;left:200px;top:17px;display:flex;align-items:center;gap:8px}
.brand-dot{width:30px;height:30px;border-radius:50%;background:var(--teal)}
.brand-name{font-family:"Poppins",sans-serif;font-weight:600;font-size:19px;color:var(--navy)}
.auth{position:absolute;left:918px;top:8px;display:flex;align-items:center;gap:8px;font-size:10px}
.auth .login{color:#222}
.auth .signup{background:var(--teal);color:#fff;padding:5px 8px;border-radius:2px}
.search{position:absolute;left:822px;top:36px;width:179px;height:26px;border:1px solid #c6c6c6;background:#fff;font-size:9px;color:#888;padding:7px 6px}
.search svg{position:absolute;right:5px;top:4px}
.hero-photo{position:absolute;left:245px;top:260px;width:710px;height:252px;background:linear-gradient(180deg,#f4f4f6 0%,#e3e3e8 100%);border-radius:4px}
.hero-title{position:absolute;left:242px;top:168px;font-family:"Poppins",sans-serif;font-weight:600;font-size:52px;line-height:56px;color:var(--navy);letter-spacing:-1px;white-space:nowrap}
.hero-sub{position:absolute;left:247px;top:224px;font-family:"Poppins",sans-serif;font-size:18px;color:var(--teal);white-space:nowrap}
.arrow{position:absolute;top:258px}
.hero-rule{position:absolute;left:200px;top:527px;width:800px;height:2px;background:linear-gradient(90deg,transparent,#bbb 20%,#bbb 80%,transparent)}
.welcome-wrap{position:absolute;left:0;top:559px;width:1200px;text-align:center}
.welcome{display:inline-flex;align-items:center;gap:7px;height:42px;padding:0 2px;border-top:1px dashed #999;border-bottom:1px dashed #999;font-family:"Poppins",sans-serif;font-weight:500;font-size:26px;line-height:40px;white-space:nowrap}
.welcome .lead{color:#8c8c8c}
.welcome .mark{width:18px;height:18px;border-radius:50%;background:var(--teal);flex:none}
.welcome .name{color:var(--navy)}
.intro{position:absolute;left:200px;top:616px;width:800px;text-align:center;font-size:9.6px;line-height:11.6px;color:var(--body-text);letter-spacing:.1px}
.intro p{margin-bottom:11.5px}
.section-rule{position:absolute;left:190px;top:762px;width:820px;height:1px;background:linear-gradient(90deg,transparent,#ddd 20%,#ddd 80%,transparent)}
.col{position:absolute;top:781px}
.col h2{font-family:"Poppins",sans-serif;font-weight:600;font-size:21px;color:var(--navy);letter-spacing:-.3px;margin-bottom:10px;white-space:nowrap}
.col h2 span{color:var(--teal)}
.col .date{font-size:9px;color:#999;margin-bottom:4px}
.col h3{font-weight:400;font-size:13px;color:var(--teal);margin-bottom:4px;white-space:nowrap}
.col p{font-size:9px;line-height:11.8px;color:var(--body-text)}
.col .author{font-size:13px;color:#111;margin-top:5px}
.col .more{position:absolute;top:128px;font-size:13px;color:#222;white-space:nowrap}
.col .more span{color:var(--teal)}
.col-posts{left:201px;width:220px}
.col-testimonials{left:515px;width:210px}
.col-comments{left:805px;width:195px}
.col-comments .item{border-bottom:1px solid var(--rule);padding-bottom:5px;margin-bottom:6px}
.col-comments .item + .item{border-bottom:0}
.quote{position:relative;padding-left:12px}
.quote::before{content:"\201C";position:absolute;left:0;top:-3px;font-size:20px;line-height:20px;color:#ccc;font-family:Georgia,serif}
.divider{position:absolute;top:787px;width:1px;height:133px;background:var(--rule)}
.footer{position:absolute;left:0;top:945px;width:1200px;height:122px;background:var(--footer-bg)}
.footer-brand{position:absolute;left:0;width:1200px;top:17px;display:flex;justify-content:center;align-items:center;gap:6px}
.footer-brand .dot{width:20px;height:20px;border-radius:50%;background:var(--icon-grey)}
.footer-brand .name{font-family:"Poppins",sans-serif;font-weight:600;font-size:13px;color:#444}
.social{position:absolute;left:0;width:1200px;top:61px;display:flex;justify-content:center;gap:5px}
.social span{width:22px;height:22px;border-radius:50%;background:var(--icon-grey)}
.copy{position:absolute;left:0;width:1200px;top:92px;text-align:center;font-size:10px;color:#333}
</style>
</head>
<body>
<nav class="nav"><ul>
  <li>Home</li><li>About Us</li><li>Software Training and Implementation</li><li>Project Management</li><li>Business Process Analysis</li><li>Blog</li><li>Contact Us</li>
</ul></nav>

<header class="header">
  <div class="brand"><span class="brand-dot"></span><span class="brand-name">VelmarqStudio</span></div>
  <div class="auth"><span class="login">Login</span><span class="signup">SignUp</span></div>
  <div class="search">Search
    <svg width="18" height="18" viewBox="0 0 18 18"><circle cx="7.5" cy="7.5" r="5.5" fill="none" stroke="#14b3c4" stroke-width="2.2"/><line x1="11.5" y1="11.5" x2="16" y2="16" stroke="#14b3c4" stroke-width="2.6" stroke-linecap="round"/></svg>
  </div>
</header>

<section class="hero">
  <div class="hero-photo" role="img" aria-label="Business people with laptops around a white bar chart with an orange rising growth arrow"></div>
  <h1 class="hero-title">Lorem Ipsum Dolor</h1>
  <p class="hero-sub">Consectetuer adipiscing elit sed diam nonummy</p>
  <svg class="arrow" style="left:160px" width="42" height="78" viewBox="0 0 42 78"><polyline points="40,1 2,39 40,77" fill="none" stroke="#9a9a9a" stroke-width="1"/></svg>
  <svg class="arrow" style="left:998px" width="42" height="78" viewBox="0 0 42 78"><polyline points="2,1 40,39 2,77" fill="none" stroke="#9a9a9a" stroke-width="1"/></svg>
  <div class="hero-rule"></div>
</section>

<section>
  <div class="welcome-wrap">
    <h2 class="welcome"><span class="lead">Welcome to</span><span class="mark"></span><span class="name">VELMARQ STUDIO</span></h2>
  </div>
  <div class="intro">
    <p>Cloud computing spending is due to account for a third of annual IT expenditure growth by the end of 2013. Every year the range of cloud software systems gets bigger, now including Brindlepath Accounting, Nimbra Suite for Business, Tradevine Job Management Software, Deskwell Office Suite, Orbitask Project Manager and many more.</p>
    <p>Signing up for cloud software is only the first part of the process, and then it has to be implemented into your business. That's where Velmarq Studio comes in.</p>
    <p>Formed in 2011, and with a history in cloud computing, implementation and support, we know there's much more to software implementation and effective business use than the purchase. We can assist by providing an external resource to assist with implementation, as well as getting the right processes post-implementation. Cloud software brings with it a huge array of benefits and efficiencies, but only if resourced and implemented correctly.</p>
    <p>Do you have somebody in your business that you can afford not to work in their role in order to implement? Having seen the negative impact this can have, we are there to help.</p>
  </div>
  <div class="section-rule"></div>
</section>

<section>
  <div class="col col-posts">
    <h2>Recent <span>Posts</span></h2>
    <div class="date">25-07-2013</div>
    <h3>Lorem ipsum dolor sit amet.</h3>
    <p>Morbi tincidunt ipsum id enim vehicula lobortis. Duis feugiat eget augue eget dictum. In iaculis nec dolor non vestibulum. Vestibulum hendrerit molestie ligula in pretium. Phasellus cursus ipsum.</p>
    <div class="more">View <span>More</span></div>
  </div>
  <div class="divider" style="left:466px"></div>
  <div class="col col-testimonials">
    <h2>Testimonials</h2>
    <h3>Lorem ipsum dolor sit amet.</h3>
    <p class="quote">Morbi tincidunt ipsum id enim vehicula lobortis. feugiat eget augue eget dictum. In iaculis nec lipsum. ”</p>
    <div class="author">Miles Harrow</div>
    <div class="more">View <span>More</span></div>
  </div>
  <div class="divider" style="left:760px"></div>
  <div class="col col-comments">
    <h2>Recent <span>Comments</span></h2>
    <div class="item"><h3>Lorem ipsum dolor sit amet.</h3><p>Morbi tincidunt ipsum id enim vehicula lobortis.</p></div>
    <div class="item"><h3>Lorem ipsum dolor sit amet.</h3><p>Morbi tincidunt ipsum id enim vehicula lobortis.</p></div>
    <div class="more">View <span>More</span></div>
  </div>
</section>

<footer class="footer">
  <div class="footer-brand"><span class="dot"></span><span class="name">VelmarqStudio</span></div>
  <div class="social" aria-label="Social links"><span></span><span></span><span></span><span></span></div>
  <p class="copy">Copyright 2013 VelmarqStudio &nbsp;|&nbsp; Privacy Policy &nbsp;|&nbsp; Terms &amp; Conditions</p>
</footer>
</body>
</html>
```